Lumra Learning Web Design Project

Who We are:
Lumra Learning is education information portal/ magazine, providing information about the Chinese and International education markets. Our aim is to help school principals improve there curriculum, and parents in understanding this curriculum.

Project Brief:
The site will include education news updates, educational services, curriculum developments and overseas study. We hope the site represents the cross cultural bridge between the west and east. The site will cover both the Sciences and Arts.

Note:
The logo design competition is also underway so we only need the website design

What We want:
This competition is for Design only no coding!
Design a home page based on Template 1,2 or 3. I only need to select one.
The design of an article page.

Optional
Design a Parvex Shutters metro style splash page.

Sites We like:
http://www.qv.com.cn/tonguebridge/default.aspx
http://www.dailyuniversitybulletin.co.uk/
http://kptz.sinocraftlearn.net/

Template Explanations:
Template 1-
The main information has a dynamic sliding category view that when clicked displays the relevant info.
In addition to the main upper menu it also has a left hand sliding menu that pops out on click or gesture

Template 2-
Has limited number of Articles most of the menus are drop downs from the top menu

Template 3-
No Top menu

Target Market(s)

Teachers, principals and parents

Industry/Entity Type

Education

Requirements
Should not have
• kindergarten preschool feel

```html
<!DOCTYPE html>
<html lang="en">
<head>
<meta charset="utf-8">
<title>Lumra Learning – Home</title>
<link href="https://fonts.googleapis.com/css2?family=Ubuntu:wght@400;500;700&family=Oswald:wght@500;700&display=swap" rel="stylesheet">
<style>
:root{
  --page:#2e2f30;
  --footer:#303132;
  --white:#ffffff;
  --red:#d9262a;
  --blue:#1f5d95;
  --blue-dark:#123a63;
  --text-red:#d0312d;
  --link-blue:#1b5aa0;
  --nav-text:#2b2b2b;
  --orange:#e8731c;
  --foot-text:#c9c9c9;
  --foot-link:#a9a9a9;
  --share-bg:#3c3d3f;
}
*{box-sizing:border-box;margin:0;padding:0}
html,body{width:955px;height:1200px;overflow:hidden}
body{position:relative;background:var(--page);font-family:'Ubuntu',sans-serif;color:var(--nav-text)}
.abs{position:absolute}

/* header */
.header{left:80px;top:24px;width:796px;height:117px;background:var(--white)}
.logo{left:16px;top:26px;display:flex;align-items:center;gap:8px}
.logo-dot{width:28px;height:28px;border-radius:50%;background:var(--blue)}
.logo-name{font-size:17px;font-weight:500;color:var(--red)}
.search{left:490px;top:26px;width:253px;height:28px;border:1px solid #d8d8d8;border-radius:2px;font-size:9px;font-style:italic;color:#9a9a9a;padding:8px 9px}
.search-btn{left:749px;top:26px;width:31px;height:27px;background:var(--red);border-radius:2px}
.nav{left:0;top:80px;width:796px;height:37px;border-top:1px solid #e5e5e5;display:flex}
.nav a{flex:1;display:flex;align-items:center;justify-content:center;font-size:12px;font-weight:500;color:var(--nav-text);text-decoration:none}
.nav a.active{background:linear-gradient(#2f6ea8,#174a7e);color:var(--white);flex:0 0 113px}

/* side rail */
.rail{left:80px;top:150px;width:48px}
.rail-btn{width:48px;height:55px;margin-bottom:3px;background:var(--red);border:1px solid #f06a6a;display:flex;align-items:center;justify-content:center}
.share-rail{left:80px;width:48px;height:26px;display:flex;align-items:center;justify-content:center;gap:4px;font-size:9px;font-weight:700;color:var(--white);letter-spacing:.2px}

/* content panel */
.panel{left:136px;top:150px;width:740px;height:799px;background:var(--white)}
.slide{left:144px;top:158px;width:588px;height:239px;background:linear-gradient(90deg,#e9e6e2 0%,#8a7f74 30%,#5a5450 55%,#3d3b3a 100%)}
.slide-title{left:428px;top:210px;width:300px;font-size:27px;font-weight:700;line-height:35px;color:var(--white);text-shadow:0 1px 3px rgba(0,0,0,.6)}
.read-more{left:430px;top:286px;width:80px;height:30px;background:var(--red);border-radius:3px;color:var(--white);font-size:13px;font-weight:500;display:flex;align-items:center;justify-content:center}

.cat-bar{left:144px;top:405px;width:588px;height:33px;background:linear-gradient(#3a7cb8,#1b4f85);color:var(--white);font-size:18px;font-weight:500;padding:4px 12px}
.fold{width:0;height:0;border-style:solid;border-width:0 8px 8px 0}
.cards{left:152px;top:448px;width:572px;height:336px;display:grid;grid-template-columns:281px 281px;column-gap:10px}
.card{height:174px}
.card-img{height:100px;box-shadow:0 1px 3px rgba(0,0,0,.35)}
.card-text{margin:10px 2px 0;font-size:11px;line-height:14.5px;color:var(--text-red);height:31px}
.view-all{margin:6px 2px 0;font-size:10.5px;font-weight:700;color:var(--link-blue)}

.band{left:144px;width:588px;height:33px;font-size:18px;font-weight:700;color:#2a2a2a;text-shadow:0 1px 0 rgba(255,255,255,.45)}
.band span{position:absolute;top:0;height:33px;line-height:33px;width:140px;text-align:center}
.band span:first-child{left:158px}
.band span:last-child{left:308px}

/* ads */
.ad-site{left:740px;top:158px;width:127px;height:477px;background:linear-gradient(#b23b30,#8e1c18 20%,#d9d5d3 45%,#9d2520 70%,#7d1412);color:var(--white);font-family:'Oswald',sans-serif;text-align:center}
.ad-brand{margin-top:12px;font-size:17px;font-weight:700}
.ad-tag{margin-top:10px;font-size:14px;line-height:15px;font-weight:500}
.ad-box{left:20px;top:140px;width:87px;height:125px;background:linear-gradient(135deg,#2a2a2a,#b03020 60%,#e28a2c)}
.ad-list{left:20px;top:326px;text-align:left;font-size:11.5px;line-height:17px;font-weight:500}
.ad-list li{list-style:none}
.ad-list li::before{content:"✓ ";color:#f0a0a0}
.ad-dl{left:18px;top:419px;width:91px;height:47px;border-radius:6px;background:linear-gradient(#3a3a3a,#0d0d0d);border:2px solid #e8e8e8;font-size:15px;line-height:15px;font-weight:700;padding-top:8px}
.ad-parent{left:740px;top:643px;width:127px;height:287px;background:var(--white);border:1px solid #ddd}
.ad-parent-art{left:0;top:0;width:125px;height:172px;background:linear-gradient(#e8e8e8,#c9c3bb)}
.ad-parent-foot{left:0;top:172px;width:125px;height:113px;background:var(--orange);color:var(--white);padding:24px 7px;font-size:13px;line-height:13px;font-weight:700}
.partner{top:69px;width:24px;height:24px;background:rgba(255,255,255,.85)}

/* footer */
.footer{left:0;top:960px;width:955px;height:240px;background:var(--footer)}
.fcol{top:26px;color:var(--foot-text)}
.fcol h3{font-size:13px;font-weight:400;margin-bottom:14px}
.fcol a{display:block;font-size:9px;line-height:16.8px;color:var(--foot-link);text-decoration:underline}
.share-row{left:651px;top:57px;display:flex;gap:8px}
.share-btn{height:26px;padding:0 9px;border-radius:2px;background:var(--share-bg);border:1px solid #4d4e50;display:flex;align-items:center;font-size:10px;font-weight:500;color:var(--white)}
.news-input{left:651px;top:126px;width:144px;height:25px;background:#262728;border:1px solid #3b3b3b;font-size:8.5px;font-style:italic;color:#777;padding:7px 9px}
.news-btn{left:795px;top:126px;width:66px;height:25px;background:var(--red);color:var(--white);font-size:10.5px;display:flex;align-items:center;justify-content:center}
.frule{left:95px;top:194px;width:765px;height:1px;background:#4a4a4a}
.copy{left:95px;top:211px;font-size:9.5px;color:#aaa}
</style>
</head>
<body>

<header class="abs header">
  <div class="abs logo"><span class="logo-dot"></span><span class="logo-name">Lumra Learning</span></div>
  <div class="abs search">Please enter your search</div>
  <div class="abs search-btn">
    <svg width="31" height="27" viewBox="0 0 31 27"><circle cx="14.5" cy="12.5" r="5" fill="none" stroke="#fff" stroke-width="2"/><line x1="18" y1="16" x2="21" y2="19" stroke="#fff" stroke-width="2"/></svg>
  </div>
  <nav class="abs nav">
    <a class="active" href="#">Home</a><a href="#">About Us</a><a href="#">Service</a><a href="#">New &amp; Event</a><a href="#">Blog</a><a href="#">Lumra Learning</a><a href="#">Contact Us</a>
  </nav>
</header>

<div class="abs panel"></div>

<div class="abs rail">
  <div class="rail-btn"><svg width="30" height="30" viewBox="0 0 30 30" fill="none" stroke="#fff" stroke-width="2.2"><path d="M3 14 L15 3 L27 14 M7 11 V26 H14"/><ellipse cx="21" cy="21" rx="7" ry="4"/><circle cx="21" cy="21" r="1.6" fill="#fff"/></svg></div>
  <div class="rail-btn"><svg width="30" height="30" viewBox="0 0 30 30" fill="#fff"><ellipse cx="12" cy="14" rx="10" ry="7"/><path d="M6 19 L4 25 L11 20Z"/><ellipse cx="20" cy="11" rx="8" ry="6" fill="none" stroke="#fff" stroke-width="2"/></svg></div>
  <div class="rail-btn"><svg width="30" height="30" viewBox="0 0 30 30" stroke="#fff" stroke-width="3.5" stroke-linecap="round"><line x1="6" y1="6" x2="24" y2="24"/><line x1="24" y1="6" x2="6" y2="24"/></svg></div>
  <div class="rail-btn"><svg width="30" height="30" viewBox="0 0 30 30" fill="none" stroke="#fff" stroke-width="2"><path d="M7 3 H19 L24 8 V27 H7Z"/><line x1="11" y1="14" x2="20" y2="14"/><line x1="11" y1="18" x2="20" y2="18"/><line x1="11" y1="22" x2="20" y2="22"/></svg></div>
  <div class="rail-btn"><svg width="30" height="30" viewBox="0 0 30 30" fill="none" stroke="#fff" stroke-width="2"><rect x="3" y="5" width="24" height="20"/><line x1="3" y1="10" x2="27" y2="10"/><rect x="7" y="14" width="7" height="7" fill="#fff"/><line x1="17" y1="15" x2="23" y2="15"/><line x1="17" y1="19" x2="23" y2="19"/></svg></div>
  <div class="rail-btn"><svg width="30" height="30" viewBox="0 0 30 30" fill="none" stroke="#fff" stroke-width="2"><rect x="4" y="4" width="22" height="14"/><line x1="8" y1="9" x2="16" y2="9"/><line x1="8" y1="13" x2="20" y2="13"/><line x1="2" y1="20" x2="28" y2="20"/><path d="M15 20 V23 M15 23 L9 28 M15 23 L21 28"/></svg></div>
  <div class="rail-btn"><svg width="30" height="30" viewBox="0 0 30 30" fill="#fff"><path d="M8 4 L12 9 L9 13 Q12 18 17 21 L21 18 L26 22 L22 27 Q13 26 5 16 Q3 9 8 4Z"/></svg></div>
</div>

<div class="abs share-rail" style="top:649px">
  <svg width="14" height="14" viewBox="0 0 14 14" fill="none" stroke="#fff" stroke-width="2"><circle cx="2.5" cy="11.5" r="1.5" fill="#fff" stroke="none"/><path d="M1 6 A7 7 0 0 1 8 13"/><path d="M1 1 A12 12 0 0 1 13 13"/></svg>
</div>
<div class="abs share-rail" style="top:694px">Social</div>
<div class="abs share-rail" style="top:740px">Circle</div>
<div class="abs share-rail" style="top:786px">Call</div>
<div class="abs share-rail" style="top:831px">Video</div>
<div class="abs share-rail" style="top:877px">Photo</div>
<div class="abs share-rail" style="top:923px">Posts</div>

<div class="abs slide" role="img" aria-label="Student holding a red notebook in a library aisle"></div>
<div class="abs slide-title">Contrairement à unei nion répandue</div>
<div class="abs read-more">Read More</div>

<div class="abs cat-bar">Categories</div>
<div class="abs fold" style="left:144px;top:438px;border-color:transparent var(--blue-dark) transparent transparent"></div>

<section class="abs cards">
  <article class="card">
    <div class="card-img" role="img" aria-label="Group of smiling students" style="background:linear-gradient(90deg,#4a3a2e,#b88d6e,#3b3230)"></div>
    <p class="card-text">Plusieurs variations de Lorem Ipsumpeuve nt être trouvées ici ou.</p>
    <p class="view-all">View All »</p>
  </article>
  <article class="card">
    <div class="card-img" role="img" aria-label="Student reading at a desk by a window" style="background:linear-gradient(90deg,#b7a896,#d9d4c8,#e9ecea)"></div>
    <p class="card-text">De nombreuses suites logicielles de mise en page ou éditeurs de sites Web.</p>
    <p class="view-all">View All »</p>
  </article>
  <article class="card">
    <div class="card-img" role="img" aria-label="Student working on a laptop" style="background:linear-gradient(90deg,#6b5e55,#a5a3a0,#6b6c6e)"></div>
    <p class="card-text">Letraset contenant des passages duLorem Ipsum, et, plus récemment.</p>
    <p class="view-all">View All »</p>
  </article>
  <article class="card">
    <div class="card-img" role="img" aria-label="Graduate in cap smiling" style="background:linear-gradient(90deg,#2a2a2a,#b58a6c,#e6ddd3)"></div>
    <p class="card-text">Suprêmes Maux) de Cicéron. Cet ouvrage, très popul aire pendant la.</p>
    <p class="view-all">View All »</p>
  </article>
</section>

<div class="abs band" style="top:793px;background:linear-gradient(#f8de2c,#e8c00a)"><span>Europe</span><span>Drama</span></div>
<div class="abs band" style="top:828px;background:linear-gradient(#4cbb49,#2e952e)"><span>Asia</span><span>Science</span></div>
<div class="abs band" style="top:863px;background:linear-gradient(#f08a2c,#dc6714)"><span>Usa</span><span>English</span></div>
<div class="abs band" style="top:898px;background:linear-gradient(#e6443d,#cc2722)"><span>France</span><span>Franch</span></div>
<div class="abs fold" style="left:144px;top:826px;border-color:transparent #9a8307 transparent transparent"></div>
<div class="abs fold" style="left:144px;top:861px;border-color:transparent #1e6a1e transparent transparent"></div>
<div class="abs fold" style="left:144px;top:896px;border-color:transparent #9c4a0c transparent transparent"></div>
<div class="abs fold" style="left:144px;top:931px;border-color:transparent #8a1612 transparent transparent"></div>

<aside class="abs ad-site">
  <div class="ad-brand">SiteForge 5</div>
  <div class="ad-tag">Create<br>your website<br>in just<br>5 steps</div>
  <div class="abs ad-box" role="img" aria-label="Software product box"></div>
  <ul class="abs ad-list"><li>1400 Templates</li><li>Webshop</li><li>RSS feed</li><li>Member Areas</li><li>Blog</li></ul>
  <div class="abs ad-dl">DOWNLOAD<br>IT NOW!</div>
</aside>

<aside class="abs ad-parent">
  <div class="abs ad-parent-art" role="img" aria-label="Cartoon family characters"></div>
  <div class="abs ad-parent-foot">800-555-0142<br>Parentwise.org
    <div class="abs partner" style="left:4px"></div>
    <div class="abs partner" style="left:34px"></div>
    <div class="abs partner" style="left:64px"></div>
    <div class="abs partner" style="left:97px"></div>
  </div>
</aside>

<footer class="abs footer">
  <div class="abs fcol" style="left:95px"><h3>Company</h3><a>Contrairement</a><a>Opinion répandue</a><a>Pas simplement du</a><a>Texte aléatoire</a></div>
  <div class="abs fcol" style="left:233px"><h3>Dictionnaire de</h3><a>Plusieurs variations</a><a>De Lorem Ipsum</a><a>Vent être</a></div>
  <div class="abs fcol" style="left:379px"><h3>Trouvées ici ou</h3><a>Siècle est reproduit</a><a>Dessous pour les</a><a>CurieuxPlusieurs varia-</a><a>tions</a><a>De Lorem Ipsum</a></div>
  <div class="abs fcol" style="left:521px"><h3>Embarassantes</h3><a>L'extrait standard</a><a>Utilisé depuis</a><a>Siècle est reproduit</a><a>Dessous pour les</a><a>Curieux</a><a>Vous voulez utiliser</a><a>Passage du Lorem</a></div>
  <div class="abs fcol" style="left:651px"><h3>Stay updates on our Socail Network</h3></div>
  <div class="abs share-row">
    <span class="share-btn">Social</span>
    <span class="share-btn">Posts</span>
    <span class="share-btn">Jobs</span>
  </div>
  <div class="abs fcol" style="left:651px;top:105px"><h3>Join Our Newsletter</h3></div>
  <div class="abs news-input">Enter your email address</div>
  <div class="abs news-btn">Subscribe</div>
  <div class="abs frule"></div>
  <div class="abs copy">© Copyrights 2013 All rights Reserved</div>
</footer>

</body>
</html>
```